Public Speaking Book for aspiring, ambitious speakers

I'm looking for a 6x9 book cover (Brivora standard) as well as ebook and audiobook formats.

I'm looking for orange font on a white background as these are my brand colours.

Feel free to use some yellow and gold too if you deem it appropriate.

Title: Climb and Kindle
Subtitle: Find Your Voice. Tell Your Story. Share your Message.
Author: Owen Thistlewood

I would like to have a picture of a female speaker on the front cover.

Alternatively, some kind of image that symbolises public speaking like a microphone, podium etc

Target Market(s)

Aspiring professional speakers

Colors
f78f20

Requirements
Must have
• Correct spelling!
Nice to have
• A logo or picture that fits the theme, but no pressure if you can't think of anything
Should not have
• No men in suits please. I don't want this to have a 1980s corporate look.

```html
<!DOCTYPE html>
<html lang="en">
<head>
<meta charset="utf-8">
<title>Climb and Kindle — Book Cover Wrap</title>
<link href="https://fonts.googleapis.com/css2?family=Bebas+Neue&family=Raleway:wght@400;500;700;800&display=swap" rel="stylesheet">
<style>
  :root {
    --orange: #f78f20;
    --orange-mid: #f9a54e;
    --orange-light: #fbc78f;
    --paper: #ffffff;
    --ink: #222222;
    --rule: #8a8a8a;
    --stage: #2d2d2d;
  }
  * { margin: 0; padding: 0; box-sizing: border-box; }
  html, body {
    width: 1200px; height: 1200px; overflow: hidden;
    background: var(--stage);
  }
  .canvas { position: relative; width: 1200px; height: 1200px; }
  .cover-wrap {
    position: absolute; left: 69px; top: 240px;
    width: 1020px; height: 719px; background: var(--paper);
  }
  .back-flap {
    position: absolute; left: 0; top: 0; width: 195px; height: 719px;
    background: var(--paper);
  }
  .back-panel {
    position: absolute; left: 195px; top: 0; width: 285px; height: 719px;
    background: var(--orange);
  }
  .blurb {
    font-family: "Raleway", sans-serif;
    text-align: justify; hyphens: auto;
  }
  .blurb p { margin-bottom: 6px; }
  .blurb--flap {
    position: absolute; left: 37px; top: 185px; width: 138px;
    font-size: 9.6px; line-height: 1.15; color: var(--ink);
  }
  .blurb--panel {
    position: absolute; left: 20px; top: 30px; width: 229px;
    font-size: 11.6px; line-height: 1.16; color: var(--paper);
  }
  .artwork { position: absolute; left: 0; top: 0; width: 1200px; height: 1200px; pointer-events: none; }
  .title { font-family: "Bebas Neue", sans-serif; fill: var(--orange); }
  .title-and { font-family: "Raleway", sans-serif; font-weight: 800; fill: var(--ink); }
  .tagline { font-family: "Raleway", sans-serif; font-weight: 500; font-size: 20px; fill: var(--ink); }
  .author { font-family: "Raleway", sans-serif; font-weight: 700; fill: #2b2b2b; }
</style>
</head>
<body>
<main class="canvas">
  <section class="cover-wrap">
    <div class="back-flap">
      <div class="blurb blurb--flap">
        <p>Lorem ipsum dolor sit amet, consectetuer adipiscing elit, sed diam nonummy nibh euismod tincidunt ut laoreet dolore magna aliquam erat volutpat. Ut wisi enim ad minim veniam, quis nostrud exerci tation ullamcorper suscipit lobortis nisl ut aliquip ex ea commodo consequat. Duis autem vel eum iriure dolor in hendrerit in vulputate velit esse molestie consequat, vel illum dolore eu feugiat nulla facilisis at vero eros et accumsan et iusto odio dignissim qui blandit praesent luptatum zzril delenit augue duis dolore te feugait nulla facilisi.</p>
        <p>Lorem ipsum dolor sit amet, cons ectetuer adipiscing elit, sed diam nonummy nibh euismod tincidunt ut laoreet dolore magna aliquam erat volutpat. Ut wisi enim ad minim veniam, quis nostrud exerci tation ullamcorper suscipit lobortis nisl ut aliquip ex ea commodo consequat.</p>
        <p>Lorem ipsum dolor sit amet, consectetuer adipiscing elit, sed diam nonummy nibh euismod tincidunt ut laoreet dolore magna aliquam erat volutpat. Ut wisi enim ad minim veniam, quis nostrud exerci tation ullamcorper suscipit lobortis nisl ut aliquip ex ea commodo consequat. Duis autem vel eum iriure dolor in hendrerit in vulputate velit esse molestie consequat, vel illum dolore eu feugiat nulla facilisis at</p>
      </div>
    </div>
    <div class="back-panel">
      <div class="blurb blurb--panel">
        <p>Lorem ipsum dolor sit amet, consectetuer adipiscing elit, sed diam nonummy nibh euismod tincidunt ut laoreet dolore magna aliquam erat volutpat. Ut wisi enim ad minim veniam, quis nostrud exerci tation ullamcorper suscipit lobortis nisl ut aliquip ex ea commodo consequat. Duis autem vel eum iriure dolor in hendrerit in vulputate velit esse molestie consequat, vel illum dolore eu feugiat nulla facilisis at vero eros et accumsan et iusto odio dignissim qui blandit praesent luptatum zzril delenit augue duis dolore te feugait nulla facilisi.</p>
        <p>Lorem ipsum dolor sit amet, cons ectetuer adipiscing elit, sed diam nonummy nibh euismod tincidunt ut laoreet dolore magna aliquam erat volutpat. Ut wisi enim ad minim veniam, quis nostrud exerci tation ullamcorper suscipit lobortis nisl ut aliquip ex ea commodo consequat.</p>
        <p>Lorem ipsum dolor sit amet, consectetuer adipiscing elit, sed diam nonummy nibh euismod tincidunt ut laoreet dolore magna aliquam erat volutpat. Ut wisi enim ad minim veniam, quis nostrud exerci tation ullamcorper suscipit lobortis nisl ut aliquip ex ea commodo consequat. Duis autem vel eum iriure dolor in hendrerit in vulputate velit esse molestie consequat, vel illum dolore eu feugiat nulla facilisis at vero eros et accumsan et iusto odio dignissim qui blandit praesent luptatum zzril delenit augue duis dolore te feugait nulla facilisi.</p>
        <p>Lorem ipsum dolor sit amet, cons ectetuer adipiscing elit, sed diam nonummy nibh euismod tincidunt ut laoreet dolore magna aliquam erat volutpat. Ut wisi enim ad minim veniam, quis nostrud exerci tation ullamcorper suscipit lobortis nisl ut aliquip ex ea commodo conse-</p>
      </div>
    </div>
  </section>

  <svg class="artwork" viewBox="0 0 1200 1200" width="1200" height="1200" aria-label="Climb and Kindle by Owen Thistlewood">
    <!-- front bottom bands -->
    <polygon points="549,878 844,878 1089,772 1089,959 549,959" fill="var(--orange-light)"/>
    <polygon points="549,959 1089,822 1089,959" fill="var(--orange-mid)"/>
    <polygon points="618,959 1089,830 1089,959" fill="var(--orange)"/>

    <!-- back flap title -->
    <text class="title" x="106" y="342" font-size="103" textLength="138" lengthAdjust="spacingAndGlyphs">CLIMB</text>
    <line x1="106" y1="353" x2="162" y2="353" stroke="var(--rule)" stroke-width="0.8"/>
    <line x1="188" y1="353" x2="244" y2="353" stroke="var(--rule)" stroke-width="0.8"/>
    <text class="title-and" x="175" y="356" font-size="8" text-anchor="middle" letter-spacing="1">AND</text>
    <text class="title" x="106" y="409" font-size="72" textLength="138" lengthAdjust="spacingAndGlyphs">KINDLE</text>

    <!-- spine -->
    <text transform="rotate(90 566 389)" x="566" y="389" font-size="56" textLength="275" lengthAdjust="spacingAndGlyphs">
      <tspan class="title">CLIMB </tspan><tspan class="title-and" font-size="26">AND </tspan><tspan class="title">KINDLE</tspan>
    </text>
    <text class="author" transform="rotate(90 577 770)" x="577" y="770" font-size="20" textLength="150" lengthAdjust="spacingAndGlyphs">OWEN THISTLEWOOD</text>

    <!-- front title -->
    <text class="title" x="642" y="458" font-size="285" textLength="422" lengthAdjust="spacingAndGlyphs">CLIMB</text>
    <line x1="644" y1="516" x2="808" y2="516" stroke="var(--ink)" stroke-width="1.2"/>
    <line x1="898" y1="516" x2="1061" y2="516" stroke="var(--ink)" stroke-width="1.2"/>
    <text class="title-and" x="853" y="524" font-size="22" text-anchor="middle" letter-spacing="3">AND</text>
    <text class="title" x="642" y="678" font-size="196" textLength="422" lengthAdjust="spacingAndGlyphs">KINDLE</text>

    <!-- subtitle -->
    <g stroke="var(--rule)" stroke-width="1">
      <line x1="674" y1="697" x2="1023" y2="697"/>
      <line x1="674" y1="747" x2="1023" y2="747"/>
      <line x1="674" y1="798" x2="1023" y2="798"/>
      <line x1="674" y1="848" x2="1023" y2="848"/>
    </g>
    <text class="tagline" x="712" y="730" textLength="271" lengthAdjust="spacing">FIND YOUR VOICE</text>
    <text class="tagline" x="709" y="781" textLength="278" lengthAdjust="spacing">TELL YOUR STORY</text>
    <text class="tagline" x="674" y="832" textLength="348" lengthAdjust="spacing">SHARE YOUR MESSAGE</text>

    <!-- author -->
    <text class="author" x="1063" y="919" font-size="23" text-anchor="end">OWEN THISTLEWOOD</text>
  </svg>
</main>
</body>
</html>
```